Elevating our current Business Card Design

We want to elevate our current business card with a new design to look like a zenith 300 company. We are a premium lubricant distributor (oil and grease).
We need 2 versions, version 1 is as per the uploaded a copy of our current business card with the English version.
For our Chinese version we need to use the front to be English in English and have the back of the card designed exactly like the front for all info to be in Chinese.
The design template needs to be such that we can amend the template with adding different information for each person's card.
The background colour of the card can be changed- we just need to clearly see all information on the card and logos.
The QJR and Ember steady logos cannot have any colour or display changes- only use the logos attached.
All logos need to be included and all information from the attached current card

```html
<!DOCTYPE html>
<html lang="en">
<head>
<meta charset="utf-8">
<title>Northvale Lubricant Distributors – Business Card</title>
<link rel="stylesheet" href="https://fonts.googleapis.com/css2?family=Open+Sans:wght@400;600;700;800&family=Ubuntu:ital,wght@1,700&display=swap">
<style>
  :root {
    --canvas: #1f1f1f;
    --card: #232124;
    --red: #e8291f;
    --red-deep: #9e1a20;
    --gold: #f2b21b;
    --silver: #d7d7d9;
    --white: #ffffff;
    --badge-orange: #ee6a1c;
  }
  * { box-sizing: border-box; margin: 0; padding: 0; }
  html, body {
    width: 1200px; height: 780px; overflow: hidden;
    background: var(--canvas);
    font-family: "Open Sans", sans-serif;
    color: var(--white);
  }
  .card {
    position: absolute; top: 225px;
    width: 560px; height: 330px;
    background: var(--card);
    overflow: hidden;
    box-shadow: 0 10px 30px rgba(0,0,0,.45);
  }
  .card--front { left: 30px; }
  .card--back { left: 610px; }

  .sweep { position: absolute; inset: 0; }
  .address-text {
    font-family: "Open Sans", sans-serif; font-size: 15px; fill: var(--white);
    letter-spacing: .3px;
  }

  .brand-mark {
    position: absolute; display: flex; align-items: center; gap: 10px;
    font-family: "Open Sans", sans-serif; font-weight: 800; color: var(--red);
    letter-spacing: 1px;
  }
  .brand-mark__dot { border-radius: 50%; background: var(--gold); flex: none; }
  .card--front .brand-mark { top: 48px; right: 44px; font-size: 46px; }
  .card--front .brand-mark__dot { width: 22px; height: 22px; }

  .person { position: absolute; left: 40px; top: 40px; }
  .person__name {
    font-family: "Ubuntu", sans-serif; font-style: italic; font-weight: 700;
    font-size: 31px; color: var(--red); line-height: 1.1;
  }
  .person__role { font-size: 15px; margin-top: 4px; letter-spacing: .2px; }

  .divider {
    position: absolute; left: 292px; top: 150px;
    width: 2px; height: 80px; background: var(--white);
  }
  .contacts {
    position: absolute; left: 312px; top: 140px;
    list-style: none; font-size: 14.5px; line-height: 21px;
  }
  .contacts li { display: flex; align-items: center; gap: 10px; }
  .contacts svg { width: 14px; height: 14px; flex: none; }

  .card--back .brand-mark { top: 70px; right: 60px; font-size: 92px; gap: 16px; }
  .card--back .brand-mark__dot { width: 40px; height: 40px; }

  .partner-strip {
    position: absolute; left: 22px; bottom: 26px;
    display: flex; align-items: center; gap: 12px;
  }
  .badge { border-radius: 50%; flex: none; }
  .badge--network { width: 42px; height: 42px; background: var(--white); }
  .badge--cert {
    width: 36px; height: 36px; background: var(--badge-orange);
    border: 4px solid #8d8d90;
  }
  .distributor-box {
    display: flex; align-items: center; height: 44px;
    border: 2px solid var(--red); border-radius: 4px; overflow: hidden;
  }
  .distributor-box__name {
    padding: 0 12px; font-size: 9px; font-weight: 600; line-height: 1.2;
    text-transform: uppercase; color: var(--white); width: 150px;
  }
  .distributor-box__name strong { color: var(--red); font-size: 15px; font-weight: 800; display: block; }
  .supplier-block {
    background: var(--red); height: 100%; padding: 0 14px;
    display: flex; flex-direction: column; justify-content: center;
  }
  .supplier-block__name { font-size: 17px; font-weight: 800; letter-spacing: 1px; line-height: 1; }
  .supplier-block__tag { font-size: 8px; font-weight: 600; letter-spacing: 1px; text-transform: uppercase; }
</style>
</head>
<body>

<section class="card card--front" aria-label="Card front">
  <svg class="sweep" viewBox="0 0 560 330" aria-hidden="false">
    <defs>
      <linearGradient id="redSweep" x1="0" y1="0" x2="1" y2="1">
        <stop offset="0" stop-color="#e8291f"/>
        <stop offset=".55" stop-color="#b51d20"/>
        <stop offset="1" stop-color="#e8291f"/>
      </linearGradient>
      <path id="addressPath" d="M30,190 C140,250 300,300 520,318"/>
    </defs>
    <path d="M0,120 C110,200 280,280 560,312 L560,330 L0,330 Z" fill="url(#redSweep)"/>
    <path d="M60,118 C150,205 310,268 540,300" fill="none" stroke="var(--gold)" stroke-width="3"/>
    <text class="address-text"><textPath href="#addressPath" startOffset="4%">14 Freightway Drive Kelso, WA 6199</textPath></text>
  </svg>

  <div class="brand-mark"><span class="brand-mark__dot"></span>NVL</div>

  <div class="person">
    <p class="person__name">Mara Vellin</p>
    <p class="person__role">Administration Executive</p>
  </div>

  <div class="divider"></div>

  <ul class="contacts">
    <li><svg viewBox="0 0 16 16"><path d="M4 1l3 3-2 2c1 2 3 4 5 5l2-2 3 3-2 3C7 15 1 9 1 3z" fill="var(--red)"/></svg>1300 000 417</li>
    <li><svg viewBox="0 0 16 16"><rect x="4" y="1" width="8" height="14" rx="1.5" fill="none" stroke="var(--red)" stroke-width="1.6"/></svg>+61 400 218 764</li>
    <li><svg viewBox="0 0 16 16"><rect x="1" y="6" width="14" height="9" rx="1" fill="var(--red)"/><rect x="4" y="1" width="8" height="5" fill="none" stroke="var(--red)" stroke-width="1.4"/></svg>+61 8 9000 4412</li>
    <li><svg viewBox="0 0 16 16"><circle cx="8" cy="8" r="6.5" fill="none" stroke="var(--red)" stroke-width="1.6"/><path d="M1.5 8h13M8 1.5c-3 3-3 10 0 13M8 1.5c3 3 3 10 0 13" fill="none" stroke="var(--red)" stroke-width="1.2"/></svg>www.nvldirect.com</li>
    <li><svg viewBox="0 0 16 16"><rect x="1" y="3" width="14" height="10" rx="1" fill="var(--red)"/><path d="M1 4l7 5 7-5" fill="none" stroke="var(--card)" stroke-width="1.4"/></svg>mara.vellin@nvldirect.com</li>
  </ul>
</section>

<section class="card card--back" aria-label="Card back">
  <div class="brand-mark"><span class="brand-mark__dot"></span>NVL</div>

  <div class="partner-strip">
    <span class="badge badge--network" role="img" aria-label="Ember steady network member badge"></span>
    <span class="badge badge--cert" role="img" aria-label="QJR certification badge"></span>
    <div class="distributor-box">
      <p class="distributor-box__name"><strong>NVL</strong>Northvale Lubricant Distributors</p>
      <div class="supplier-block">
        <span class="supplier-block__name">VANTOR</span>
        <span class="supplier-block__tag">Premium Lubricants</span>
      </div>
    </div>
    <span class="badge badge--cert" role="img" aria-label="QJR certification badge"></span>
    <span class="badge badge--cert" role="img" aria-label="QJR certification badge"></span>
  </div>
</section>

</body>
</html>
```